Sophisticated, clean website reflecting my feminine, playful side to sell my abstract art,

I need a website no more than 3 pages to showcase my paintings, a little about me and some contact info. I do abstracts so looking for something a little edgy, yet feminine and current.
Updates

Hi there, These are some artists websites that I Iike: Marnelvoss.com (I like how airy it is) peterwallombry.com garethpolvens.com (I like how it scrolls) I'll need a place for a photo ( a headshot-i do not have it yet so I'll need to be able to upload that later) as well as an area for my bio. Also, it's important that I will be able to upload any new photos and descriptions easily so it should be user friendly. Lastly, I like in a sunny place so would like to have this seem upbeat and playful as that is how i like to paint. thanks-I'm trying to upload my photos now -

Target Market(s)

ppl ages 35-70 who want large scale art for their homes

Industry/Entity Type

art

Coding

Coded - Design and coding required

Number of Pages Required

3 page

Colors

Designer to choose colors to be used in the design.

Requirements
Must have
• photos of my art, a place for my bio, be easy to reach me. tasteful-nothing too "in your face" -my clients are pretty high end and organized. They like clean lines
Nice to have
• sophisticated background, muted tones in the back-similar clean font throughout-no cursive
Should not have
• too many dark areas. Too many blocks of color. Too serious.

```html
<!DOCTYPE html>
<html lang="en">
<head>
<meta charset="utf-8">
<title>Lena Marlowe Art</title>
<link href="https://fonts.googleapis.com/css2?family=Montserrat:wght@400;500;600;700;800&family=Lato:wght@400;700&display=swap" rel="stylesheet">
<style>
:root{
  --orange:#f05a24;
  --orange-soft:#f7a07c;
  --black:#000;
  --ink:#2b2b2b;
  --body:#6b6b6b;
  --frame:#d6d6d6;
  --footer:#ececec;
  --white:#fff;
  --tone-violet:#b7a6bd;
  --tone-slate:#8c9cae;
  --tone-sky:#c9dbe4;
  --tone-sage:#a9c2a8;
  --tone-stone:#b9c0bd;
  --tone-sand:#cfc3a6;
  --tone-rose:#c7aba1;
}
*{margin:0;padding:0;box-sizing:border-box}
html,body{width:1200px;height:3483px;overflow:hidden;background:var(--white)}
body{position:relative;font-family:'Montserrat',sans-serif;color:var(--ink)}
.abs{position:absolute}
/* header */
.site-header{position:absolute;left:0;top:0;width:1200px;height:115px;background:var(--black)}
.nav-link{position:absolute;top:50px;font-size:14px;font-weight:700;color:var(--white);letter-spacing:.2px}
.nav-link.active{color:var(--orange)}
.nav-link.active::after{content:"";position:absolute;left:0;right:0;top:22px;height:2px;background:var(--orange)}
.divider{position:absolute;top:22px;width:1px;height:72px;background:var(--white)}
.brand{position:absolute;left:499px;width:204px;top:28px;text-align:center;line-height:1}
.brand .top{font-size:30px;font-weight:800;color:var(--white)}
.brand .bottom{font-size:21px;font-weight:700;color:var(--orange);margin-top:3px}
.follow{position:absolute;left:726px;top:50px;font-size:14px;font-weight:700;color:var(--white)}
.social{position:absolute;width:25px;height:25px;border-radius:50%}
.s1{background:#3b5da0}.s2{background:#2fa6e0}.s3{background:#dd4b39}.s4{background:#cc2127}
/* hero */
.hero-art{position:absolute;left:481px;top:115px;width:719px;height:535px;background:linear-gradient(180deg,#5fb4de,#3f86c9)}
.hero-title{position:absolute;left:108px;top:232px;font-size:68px;font-weight:800;line-height:68px;color:#2a2a2a;text-shadow:3px 3px 4px rgba(0,0,0,.3);z-index:2}
.btn{position:absolute;background:var(--orange);color:var(--white);font-weight:700;font-size:14px;border-radius:24px;display:flex;align-items:center;justify-content:center;gap:5px;box-shadow:2px 4px 6px rgba(0,0,0,.2)}
.btn-dot{width:12px;height:12px;border-radius:50%;background:var(--white);display:inline-block;position:relative}
.btn-dot::after{content:"";position:absolute;left:3px;top:3px;border-left:5px solid var(--orange);border-top:3px solid transparent;border-bottom:3px solid transparent}
.arrow-btn{position:absolute;width:46px;height:46px;border-radius:50%;background:var(--white);box-shadow:0 3px 8px rgba(0,0,0,.2)}
.disc{position:absolute;border-radius:50%}
.disc-soft{background:var(--orange-soft)}
.disc-orange{background:var(--orange)}
.disc-black{background:var(--black)}
/* about */
.portrait{position:absolute;left:111px;top:788px;width:465px;height:425px;background:linear-gradient(180deg,#c9ccce,#7d7773);z-index:2}
.section-title{font-size:35px;font-weight:700;color:var(--ink)}
.signature{position:absolute;left:612px;top:842px;width:196px;height:34px;border-radius:4px;background:var(--orange);opacity:.85}
.copy{position:absolute;left:612px;width:476px;font-family:'Lato',sans-serif;font-size:14.5px;line-height:25.6px;color:var(--body);text-align:justify}
/* gallery */
.painting{position:absolute;background:var(--frame);padding:9px}
.painting .art{width:100%;height:100%}
.painting.featured{background:var(--orange)}
.zoom{position:absolute;left:50%;top:50%;width:46px;height:46px;margin:-23px 0 0 -23px;border-radius:50%;background:var(--orange);color:var(--white);font-size:26px;font-weight:600;display:flex;align-items:center;justify-content:center}
/* contact */
.contact-panel{position:absolute;left:111px;top:2437px;width:528px;height:594px;background:var(--orange)}
.contact-art{position:absolute;left:639px;top:2437px;width:449px;height:594px;background:linear-gradient(180deg,#8a4fa6,#c8466f)}
.contact-title{position:absolute;left:180px;top:2492px;font-size:50px;font-weight:800;color:var(--white)}
.info-icon{position:absolute;width:62px;height:62px;border-radius:50%;background:var(--white)}
.info-label{position:absolute;left:301px;font-size:23px;font-weight:700;color:var(--white)}
.info-text{position:absolute;left:301px;font-size:15px;line-height:26px;color:var(--white);width:260px}
/* footer */
.site-footer{position:absolute;left:0;top:3152px;width:1200px;height:331px;background:var(--footer)}
.foot-brand{position:absolute;left:0;width:1200px;text-align:center;line-height:1}
.foot-nav{position:absolute;top:3295px;font-size:14px;font-weight:600;color:var(--ink)}
.copyright{position:absolute;left:0;width:1200px;top:3398px;text-align:center;font-family:'Lato',sans-serif;font-size:14px;color:var(--ink)}
</style>
</head>
<body>

<header class="site-header">
  <span class="nav-link active" style="left:213px">HOME</span>
  <span class="nav-link" style="left:282px">ABOUT ME</span>
  <span class="nav-link" style="left:383px">CONTACT US</span>
  <span class="divider" style="left:499px"></span>
  <div class="brand"><div class="top">LENA</div><div class="bottom">MARLOWE ART</div></div>
  <span class="divider" style="left:703px"></span>
  <span class="follow">FOLLOW US :</span>
  <span class="social s1" style="left:826px;top:45px" aria-label="Social profile"></span>
  <span class="social s2" style="left:858px;top:45px" aria-label="Social profile"></span>
  <span class="social s3" style="left:892px;top:45px" aria-label="Social profile"></span>
  <span class="social s4" style="left:924px;top:45px" aria-label="Social profile"></span>
</header>

<section class="hero">
  <div class="disc disc-soft" style="left:442px;top:570px;width:116px;height:116px"></div>
  <div class="hero-art" role="img" aria-label="Featured abstract painting"></div>
  <h1 class="hero-title">LENA<br>MARLOWE ART</h1>
  <div class="btn" style="left:111px;top:390px;width:161px;height:47px">GET STARTED <span class="btn-dot"></span></div>
  <div class="arrow-btn" style="left:119px;top:523px">
    <svg width="46" height="46" viewBox="0 0 46 46"><path d="M26 16l-7 7 7 7" fill="none" stroke="#222" stroke-width="2"/></svg>
  </div>
  <div class="arrow-btn" style="left:187px;top:523px">
    <svg width="46" height="46" viewBox="0 0 46 46"><path d="M20 16l7 7-7 7" fill="none" stroke="#222" stroke-width="2"/></svg>
  </div>
</section>

<section class="about">
  <div class="disc disc-orange" style="left:57px;top:858px;width:116px;height:116px"></div>
  <div class="portrait" role="img" aria-label="Headshot of the artist"></div>
  <div class="disc disc-soft" style="left:91px;top:775px;width:118px;height:118px;z-index:3;opacity:.9"></div>
  <h2 class="section-title abs" style="left:612px;top:788px">ABOUT ME</h2>
  <div class="signature" role="img" aria-label="Artist signature"></div>
  <p class="copy" style="top:892px">Lorem ipsum dolor sit amet, consectetur adipiscing elit, sed do eiusmod tempor incididunt ut labore et dolore magna aliqua. Ut enim ad minim veniam, quis nostrud exercitation ullamco laboris nisi ut aliquip ex ea commodo consequat. Duis aute irure dolor in reprehenderit in voluptate velit esse cillum dolore eu fugiat nulla pariatur.</p>
  <p class="copy" style="top:1045px">Excepteur sint occaecat cupidatat non proident, sunt in culpa qui officia deserunt mollit anim id est laborum. Lorem ipsum dolor sit amet, consectetur adipiscing elit, sed do eiusmod tempor incididunt ut labore et dolore magna aliqua. Ut enim ad minim veniam</p>
  <div class="btn" style="left:612px;top:1166px;width:161px;height:47px">LEARN MORE <span class="btn-dot"></span></div>
</section>

<section class="gallery">
  <h2 class="section-title abs" style="left:388px;width:421px;top:1355px;text-align:center">MY PAINTINGS</h2>
  <div class="painting" style="left:111px;top:1355px;width:266px;height:355px"><div class="art" role="img" aria-label="Painting one" style="background:var(--tone-violet)"></div></div>
  <div class="painting featured" style="left:388px;top:1423px;width:421px;height:285px"><div class="art" role="img" aria-label="Painting two" style="background:var(--tone-slate)"></div><div class="zoom">+</div></div>
  <div class="painting" style="left:821px;top:1356px;width:267px;height:356px"><div class="art" role="img" aria-label="Painting three" style="background:var(--tone-sky)"></div></div>
  <div class="painting" style="left:111px;top:1720px;width:266px;height:357px"><div class="art" role="img" aria-label="Painting four" style="background:var(--tone-sage)"></div></div>
  <div class="painting" style="left:388px;top:1719px;width:421px;height:285px"><div class="art" role="img" aria-label="Painting five" style="background:var(--tone-stone)"></div></div>
  <div class="painting" style="left:821px;top:1720px;width:267px;height:355px"><div class="art" role="img" aria-label="Painting six" style="background:var(--tone-sand)"></div></div>
  <div class="painting" style="left:388px;top:2014px;width:421px;height:286px"><div class="art" role="img" aria-label="Painting seven" style="background:var(--tone-rose)"></div></div>
</section>

<section class="contact">
  <div class="disc disc-black" style="left:52px;top:2400px;width:118px;height:118px"></div>
  <div class="disc disc-soft" style="left:1003px;top:2400px;width:118px;height:118px"></div>
  <div class="disc disc-soft" style="left:60px;top:2940px;width:118px;height:118px"></div>
  <div class="contact-panel"></div>
  <div class="contact-art" role="img" aria-label="Colourful abstract painting"></div>
  <h2 class="contact-title">CONTACT US</h2>

  <div class="info-icon" style="left:186px;top:2589px"><svg width="62" height="62" viewBox="0 0 62 62"><path d="M31 20a8 8 0 0 0-8 8c0 6 8 14 8 14s8-8 8-14a8 8 0 0 0-8-8z" fill="#f05a24"/><circle cx="31" cy="28" r="3" fill="#fff"/></svg></div>
  <span class="info-label" style="top:2583px">ADDRESS:</span>
  <p class="info-text" style="top:2622px">123,Lorem ipsum dolor sit amet, consectetur</p>

  <div class="info-icon" style="left:186px;top:2735px"><svg width="62" height="62" viewBox="0 0 62 62"><rect x="21" y="23" width="20" height="15" fill="#f05a24"/><path d="M21 23l10 8 10-8" fill="none" stroke="#fff" stroke-width="1.5"/></svg></div>
  <span class="info-label" style="top:2729px">EMAIL ADDRESS:</span>
  <p class="info-text" style="top:2768px">info@companyname.com</p>

  <div class="info-icon" style="left:186px;top:2881px"><svg width="62" height="62" viewBox="0 0 62 62"><path d="M24 21c-3 2-3 6 0 11s8 9 12 9c2 0 4-2 4-3l-4-4-3 2c-3-1-6-5-7-7l2-3-4-5z" fill="#f05a24"/></svg></div>
  <span class="info-label" style="top:2875px">PHONE:</span>
  <p class="info-text" style="top:2914px">+1 888 888 8888</p>
</section>

<footer class="site-footer"></footer>
<div class="foot-brand" style="top:3218px;font-size:29px;font-weight:800;color:var(--orange)">LENA</div>
<div class="foot-brand" style="top:3250px;font-size:20px;font-weight:700;color:var(--ink)">MARLOWE ART</div>
<span class="foot-nav" style="left:471px">HOME</span>
<span class="foot-nav" style="left:540px">ABOUT ME</span>
<span class="foot-nav" style="left:641px">CONTACT US</span>
<span class="social s1" style="left:538px;top:3343px" aria-label="Social profile"></span>
<span class="social s2" style="left:571px;top:3343px" aria-label="Social profile"></span>
<span class="social s3" style="left:604px;top:3343px" aria-label="Social profile"></span>
<span class="social s4" style="left:638px;top:3343px" aria-label="Social profile"></span>
<p class="copyright">© Copyrights 2022 Company name | All Rights reserved</p>

</body>
</html>
```